Corvane Freight Company Business Card Design

We are a company that delivers natural saltwater (from the ocean) to aquarium companies, restaurants and home marine tanks. I would like a new business card to suit.

Must include Name, company name, abn, contact number and website as well as logo (see attached).

Looking for a design that stands out, has a clean but unique appearance.

Double and single sided entries welcome

Business

• Logo

```html
<!DOCTYPE html>
<html lang="en">
<head>
<meta charset="utf-8">
<title>Corvane Freight Company – Business Card</title>
<link rel="stylesheet" href="https://fonts.googleapis.com/css2?family=Open+Sans:wght@400;700&family=Lato:wght@400&display=swap">
<style>
  :root {
    --backdrop: #1c1c1c;
    --card-blue: #2f7ce0;
    --wave-light: #86d6f2;
    --wave-pale: #c4ecfa;
    --ink-dark: #0d0d0d;
    --ink-light: #ffffff;
    --rule: rgba(255,255,255,0.75);
  }
  html, body {
    margin: 0;
    padding: 0;
    width: 1200px;
    height: 406px;
    overflow: hidden;
    background: var(--backdrop);
  }
  .canvas {
    position: relative;
    width: 1200px;
    height: 406px;
  }
  .card {
    position: absolute;
    top: 48px;
    width: 525px;
    height: 300px;
    border-radius: 18px;
    background: var(--card-blue);
    overflow: hidden;
    color: var(--ink-light);
  }
  .card--front { left: 59px; }
  .card--back { left: 620px; }

  .brand-name {
    position: absolute;
    margin: 0;
    font-family: "Open Sans", sans-serif;
    font-weight: 700;
    color: var(--ink-light);
    white-space: nowrap;
    text-align: center;
  }
  .card--front .brand-name {
    left: 120px;
    width: 285px;
    top: 52px;
    font-size: 32px;
  }
  .card--back .brand-name {
    left: 60px;
    width: 405px;
    top: 110px;
    font-size: 42px;
  }

  .wave-band {
    position: absolute;
    left: 0;
    top: 130px;
    width: 525px;
    height: 100px;
  }

  .holder {
    position: absolute;
    left: 193px;
    top: 148px;
    margin: 0;
    font-family: "Open Sans", sans-serif;
    font-size: 17px;
    color: var(--ink-dark);
    white-space: nowrap;
  }
  .holder__name { font-weight: 700; }
  .holder__title { font-weight: 400; font-size: 14px; }

  .contact {
    position: absolute;
    top: 230px;
    font-family: "Lato", sans-serif;
    font-size: 13px;
    line-height: 18px;
    margin: 0;
    white-space: nowrap;
  }
  .contact--address {
    right: 264px;
    text-align: right;
  }
  .contact--details {
    left: 286px;
  }
  .contact__icon {
    display: inline-block;
    width: 9px;
    height: 9px;
    margin-right: 4px;
    vertical-align: -1px;
  }
  .divider {
    position: absolute;
    left: 274px;
    top: 224px;
    width: 1px;
    height: 63px;
    background: var(--rule);
  }
  .web-address {
    position: absolute;
    left: 0;
    width: 525px;
    top: 239px;
    margin: 0;
    text-align: center;
    font-family: "Lato", sans-serif;
    font-size: 15px;
    letter-spacing: 3px;
  }
</style>
</head>
<body>
<div class="canvas">

  <section class="card card--front">
    <p class="brand-name">Corvane Freight</p>

    <svg class="wave-band" viewBox="0 0 525 100" role="img" aria-label="Stylised ocean wave sweeping across the card">
      <defs>
        <linearGradient id="waveTone" x1="0" y1="0" x2="1" y2="0">
          <stop offset="0" stop-color="var(--wave-pale)"/>
          <stop offset="1" stop-color="var(--wave-light)"/>
        </linearGradient>
      </defs>
      <path d="M0 88 C 40 40, 140 18, 280 10 C 380 5, 470 8, 525 18 L 525 40 C 450 30, 360 36, 260 52 C 170 66, 100 86, 60 100 L 0 100 Z" fill="url(#waveTone)"/>
    </svg>

    <p class="holder"><span class="holder__name">Your name,</span> <span class="holder__title">Title</span></p>

    <p class="contact contact--address">
      Corvane Freight Company<br>
      Street Name, City Name<br>
      State, City Zip Code
    </p>
    <div class="divider"></div>
    <p class="contact contact--details">
      <svg class="contact__icon" viewBox="0 0 10 10" aria-hidden="true"><path d="M2 1 L4 1 L4.6 3 L3.4 4 C4 5.4 4.8 6.2 6 6.6 L7 5.4 L9 6 L9 8 C5 8.6 1.4 5 2 1 Z" fill="none" stroke="#fff" stroke-width="0.9"/></svg>123-456-7890<br>
      <svg class="contact__icon" viewBox="0 0 10 10" aria-hidden="true"><circle cx="5" cy="5" r="4.5" fill="#fff"/><path d="M0.5 5 H9.5" stroke="var(--card-blue)" stroke-width="0.9"/></svg>www.website.com<br>
      ABN : 0123456789
    </p>
  </section>

  <section class="card card--back">
    <p class="brand-name">Corvane Freight</p>
    <p class="web-address">www.website.com</p>
  </section>

</div>
</body>
</html>
```